CBD oil label, sleek, clean, serious

I need graphic design for a CBD oil company. Black and white labels for 30ml amber color dropper bottles. looking for something that stands out in its simplicity. this product will be a top of the line, highest margin due to quality of ingredients. It should look rich. other products on the shelf use a lot of color and logos. this label should be clear and stand out as a place to rest your eyes in a sea of marketing glitz.

please see the idea board.

Target Market(s)

middle to older adults

Industry/Entity Type

Health And Wellness

Font styles to use
Serif

Colors
fff5ef
cadf82

Requirements
Must have
• We want the look of elegance and like an apothecary label
• Product name will be Verdalume or Verdasoothe
• see other details on the attached idea board
Nice to have
• think Morvane and old style apothecary with a modern aesthetic
Should not have
• any reference or drawing of cannabis

```html
<!DOCTYPE html>
<html lang="en">
<head>
<meta charset="utf-8">
<title>Orvan Well Premium – Verdasoothe Full Spectrum CBD Oil Label</title>
<link rel="stylesheet" href="https://fonts.googleapis.com/css2?family=Marcellus&family=Cormorant+Garamond:wght@500;600&family=Montserrat:wght@300;400;500;600&display=swap">
<style>
  :root {
    --backdrop: #d9d9d9;
    --label: #eae5bb;
    --ink: #111111;
    --ink-soft: #444444;
    --pill-text: #ffffff;
    --ornament: #b9b28c;
  }
  * { margin: 0; padding: 0; box-sizing: border-box; }
  html, body {
    width: 1200px; height: 800px; overflow: hidden;
    background: var(--backdrop);
  }
  .canvas {
    position: relative; width: 1200px; height: 800px;
    font-family: "Montserrat", sans-serif; color: var(--ink);
  }
  .label {
    position: absolute; left: 39px; top: 41px;
    width: 970px; height: 462px;
    background: var(--label);
  }
  .abs { position: absolute; }

  /* Ingredients panel */
  .contents-title { left: 34px; top: 59px; font-weight: 600; font-size: 16px; }
  .contents-line { font-weight: 300; font-size: 13px; line-height: 16.5px; }
  .contents-a { left: 34px; top: 98px; }
  .contents-b { left: 34px; top: 159px; }
  .rule { left: 33px; width: 159px; height: 2px; background: var(--ink); }
  .rule-a { top: 144px; }
  .rule-b { top: 200px; }
  .contents-c { left: 34px; top: 214px; font-weight: 300; font-size: 15px; line-height: 19px; }
  .storage { left: 34px; top: 278px; font-size: 15.5px; font-weight: 400; }
  .ornament { left: 45px; top: 331px; width: 147px; height: 30px; }
  .size { font-size: 24px; font-weight: 400; letter-spacing: 0.3px; white-space: nowrap; }
  .size-left { left: 34px; top: 400px; }
  .size-center { left: 390px; top: 386px; }

  /* Brand panel */
  .brand { left: 386px; top: 53px; font-family: "Marcellus", serif; font-size: 49px; letter-spacing: -0.5px; line-height: 1; }
  .brand-tier { left: 391px; top: 100px; font-size: 20px; font-weight: 400; color: var(--ink-soft); letter-spacing: 0.5px; }
  .product { left: 386px; top: 181px; font-family: "Cormorant Garamond", serif; font-weight: 600; font-size: 34px; letter-spacing: 2.4px; color: #222; line-height: 1; }
  .product-desc { left: 388px; top: 228px; font-size: 23px; font-weight: 500; letter-spacing: 2.4px; line-height: 30px; }
  .flavor-pill {
    left: 390px; top: 352px; width: 195px; height: 29px;
    border-radius: 12px; background: var(--ink); color: var(--pill-text);
    font-size: 19px; letter-spacing: 1.5px; text-align: center; line-height: 29px;
  }

  /* Directions panel, set vertically */
  .directions {
    left: 798px; top: 430px; width: 392px;
    transform: rotate(-90deg); transform-origin: top left;
    list-style: none; font-size: 13px; line-height: 18.5px; font-weight: 400;
  }
  .directions li { position: relative; padding-left: 13px; }
  .directions li::before {
    content: ""; position: absolute; left: -14px; top: 4px;
    width: 10px; height: 10px; border-radius: 50%; background: #333;
  }
  .directions li + li { margin-top: 18px; text-align: justify; text-align-last: left; }
  .directions li { padding-left: 0; }
</style>
</head>
<body>
<div class="canvas">
  <section class="label">
    <h2 class="abs contents-title">Food Supplement Contains:</h2>
    <p class="abs contents-line contents-a">Full Spectrum CBD,<br>Hemp oil and Natural flavor</p>
    <div class="abs rule rule-a"></div>
    <p class="abs contents-line contents-b">CBD derived from Cannabis<br>less than 0.025 THC</p>
    <div class="abs rule rule-b"></div>
    <p class="abs contents-c">Derived from Cannabis<br>as a full spectrum oil</p>
    <p class="abs storage">Store in a cool, dark place</p>
    <svg class="abs ornament" viewBox="0 0 147 30" role="img" aria-label="Decorative scroll ornament">
      <rect x="0" y="8" width="147" height="14" rx="7" fill="var(--ornament)"/>
    </svg>
    <p class="abs size size-left">30 ml &nbsp;|&nbsp; 1000 mg</p>

    <h1 class="abs brand">ORVAN WELL</h1>
    <p class="abs brand-tier">Premium</p>
    <p class="abs product">Verdasoothe</p>
    <p class="abs product-desc">Full Spectrum<br>CBD Oil</p>
    <p class="abs flavor-pill">Mint flavor</p>
    <p class="abs size size-center">30 ml &nbsp;|&nbsp; 1000 mg</p>

    <ul class="abs directions">
      <li>Use: Shake well. Take 1 dropper to the mark twice daily. Hold under the tongue for 30 seconds. Use every day for best results. Start CBD use with a half dose and work up to full dose after 7 days.</li>
      <li>Discuss CBD use with a physician if taking other medications. Do not exceed 5 doses in a day</li>
    </ul>
  </section>
</div>
</body>
</html>
```